Business Card Design for a Personal Trainer

I need a business card design for my job as a personal trainer. It should have a unique, modern and exclusive design. On the front there should be only my logo with my name and my job. 0162/3819204 Tobias Lendhart Wiesengrundweg 14 80417 Munich Germany The most important contact information is the web adress. it can be bigger than the rest, but its not necessary. The card should be 8,5cmx5,5cm big. Font: Roboto. Colors: black, white, gray, 56c1ff.

```html
<!DOCTYPE html>
<html lang="de">
<head>
<meta charset="utf-8">
<title>Tobias Lendhart – Personal Trainer Visitenkarte</title>
<link rel="stylesheet" href="https://fonts.googleapis.com/css2?family=Roboto:wght@300;400&family=Bodoni+Moda:wght@400;500&display=swap">
<style>
  :root {
    --stage: #e4e4e2;
    --card: #111213;
    --logo-grey: #5f6164;
    --logo-grey-soft: #4a4c4f;
    --text-white: #f2f2f2;
    --photo-light: #8a8c8f;
    --photo-mid: #3a3b3d;
  }
  * { margin: 0; padding: 0; box-sizing: border-box; }
  html, body {
    width: 1200px; height: 892px; overflow: hidden;
    background: var(--stage);
  }
  .stage {
    position: relative; width: 1200px; height: 892px;
    display: flex; align-items: center; justify-content: center; gap: 40px;
  }
  .card {
    position: relative; width: 520px; height: 336px;
    background: var(--card);
    box-shadow: 0 10px 30px rgba(0,0,0,0.25);
    overflow: hidden;
  }
  .brand {
    position: absolute; display: flex; flex-direction: column; align-items: center;
    font-family: "Roboto", sans-serif; color: var(--logo-grey);
    white-space: nowrap;
  }
  .brand-name {
    display: flex; align-items: center; gap: 12px;
    font-weight: 400; font-size: 27px; letter-spacing: 2px; text-transform: uppercase;
  }
  .brand-mark { width: 12px; height: 12px; background: var(--logo-grey); }
  .brand-rule { width: 100%; height: 1px; background: var(--logo-grey-soft); margin-top: 4px; }
  .brand-job {
    font-weight: 300; font-size: 12px; letter-spacing: 5px; text-transform: uppercase;
    margin-top: 4px; color: var(--logo-grey-soft);
  }
  .card-front .brand { left: 50%; top: 142px; transform: translateX(-50%); }

  .card-back .brand { right: 36px; top: 44px; }
  .card-back .brand-name { font-size: 21px; }
  .card-back .brand-job { font-size: 10px; letter-spacing: 4px; }
  .contact {
    position: absolute; left: 34px; top: 110px;
    font-family: "Bodoni Moda", serif; color: var(--text-white);
    font-size: 15px; line-height: 19px; list-style: none;
  }
  .contact .web { font-weight: 500; font-size: 16px; }
  .portrait {
    position: absolute; right: 60px; bottom: 0; width: 220px; height: 196px;
    background: radial-gradient(ellipse closest-side at 50% 55%, var(--photo-light) 0%, var(--photo-mid) 55%, var(--card) 100%);
  }
</style>
</head>
<body>
<main class="stage">
  <section class="card card-back" aria-label="Rückseite">
    <div class="brand">
      <div class="brand-name"><span class="brand-mark"></span>Tobias Lendhart</div>
      <div class="brand-rule"></div>
      <div class="brand-job">Personal Trainer</div>
    </div>
    <ul class="contact">
      <li class="web">www.tobiaslendhart.de</li>
      <li>kontakt@tobiaslendhart.de</li>
      <li>0162/3819204</li>
      <li>Tobias Lendhart</li>
      <li>Wiesengrundweg 14</li>
      <li>80417 München</li>
    </ul>
    <div class="portrait" role="img" aria-label="Schwarz-weiß Porträtfoto des Trainers mit verschränkten Armen"></div>
  </section>

  <section class="card card-front" aria-label="Vorderseite">
    <div class="brand">
      <div class="brand-name"><span class="brand-mark"></span>Tobias Lendhart</div>
      <div class="brand-rule"></div>
      <div class="brand-job">Personal Trainer</div>
    </div>
  </section>
</main>
</body>
</html>
```